Veltrano.co - Polar Expeditions Specialists

We need a modern, visually striking business card for Veltrano.co, a company specialized in selling expedition cruises to the most remote regions on Earth, with a focus on the Arctic and Antarctica. The design should instantly communicate that the cardholder is an expert in polar travel. Use clean, premium aesthetics with cool tones like icy blue and white, possibly incorporating polar imagery (ice, glaciers, penguins, etc.)

Attached the logo

Contact Information for Business Card

Feels high-end and trustworthy.. Visually memorable — encourages people to keep it

Colors
0054AA
0677BA
7BADD7
CADEEF
E8F1F8

Requirements
Must have
• ice, glaciers, penguins, montains
Nice to have
• modern, transparente,

```html
<!DOCTYPE html>
<html lang="en">
<head>
<meta charset="utf-8">
<title>Veltrano.co – Business Card</title>
<link rel="stylesheet" href="https://fonts.googleapis.com/css2?family=Poppins:wght@400;500;600;700&display=swap">
<style>
  :root {
    --stage: #3a3a3a;
    --card: #161616;
    --brand-blue: #2f74c0;
    --edge-blue: #2f6fbf;
    --text-white: #e9e9e9;
    --art-dark: #0b0b0b;
    --art-light: #8a8a8a;
  }
  * { box-sizing: border-box; margin: 0; padding: 0; }
  html, body {
    width: 1200px; height: 791px; overflow: hidden;
    background: var(--stage);
    font-family: "Poppins", sans-serif;
  }
  .stage {
    width: 1200px; height: 791px;
    display: flex; align-items: center; justify-content: center; gap: 50px;
  }
  .card {
    position: relative;
    width: 540px; height: 309px;
    background: var(--card);
    border-bottom: 3px solid var(--edge-blue);
    box-shadow: 0 14px 30px rgba(0,0,0,.45);
    overflow: hidden;
  }
  .brand-name {
    color: var(--brand-blue);
    font-weight: 700; line-height: 1;
    letter-spacing: .3px; white-space: nowrap;
  }
  .brand-tagline {
    color: var(--brand-blue);
    font-weight: 500; margin-top: 5px; letter-spacing: .2px; white-space: nowrap;
  }

  /* Back card: contact side */
  .card-back .brand {
    position: absolute; left: 28px; top: 160px;
    display: flex; align-items: center; gap: 10px;
  }
  .brand-dot {
    width: 34px; height: 34px; border-radius: 50%;
    background: var(--brand-blue); flex: none;
  }
  .card-back .brand-name { font-size: 28px; }
  .card-back .brand-tagline { font-size: 9px; }
  .divider {
    position: absolute; left: 290px; top: 60px;
    width: 2px; height: 190px; background: var(--edge-blue);
  }
  .contact {
    position: absolute; left: 316px; top: 78px; color: var(--text-white);
  }
  .contact-name {
    color: var(--brand-blue); font-weight: 700; font-size: 20px;
    text-transform: uppercase; letter-spacing: .3px; white-space: nowrap;
  }
  .contact-role { font-size: 14px; margin-bottom: 18px; }
  .contact-list { list-style: none; font-size: 13px; line-height: 1.75; }
  .contact-list li { display: flex; align-items: center; gap: 8px; white-space: nowrap; }
  .contact-list svg { width: 12px; height: 12px; fill: var(--brand-blue); flex: none; }

  /* Front card: illustration side */
  .polar-art {
    position: absolute; left: 16px; top: 28px;
    width: 238px; height: 281px;
    border-radius: 120px 120px 0 0;
    background: linear-gradient(110deg, var(--art-dark) 35%, #3a3a3a 65%, var(--art-light) 100%);
  }
  .card-front .brand {
    position: absolute; right: 22px; bottom: 58px;
  }
  .card-front .brand-name { font-size: 40px; }
  .card-front .brand-tagline { font-size: 12px; }
</style>
</head>
<body>
<main class="stage">
  <section class="card card-back">
    <div class="brand">
      <span class="brand-dot"></span>
      <div>
        <div class="brand-name">Veltrano.co</div>
        <div class="brand-tagline">Polar Expeditions Specialists</div>
      </div>
    </div>
    <span class="divider"></span>
    <div class="contact">
      <div class="contact-name">Marcus Tellan</div>
      <div class="contact-role">President</div>
      <ul class="contact-list">
        <li><svg viewBox="0 0 24 24"><path d="M6.6 10.8a15 15 0 0 0 6.6 6.6l2.2-2.2a1 1 0 0 1 1-.25 11.4 11.4 0 0 0 3.6.57 1 1 0 0 1 1 1V20a1 1 0 0 1-1 1A17 17 0 0 1 3 4a1 1 0 0 1 1-1h3.5a1 1 0 0 1 1 1c0 1.25.2 2.45.57 3.6a1 1 0 0 1-.25 1z"/></svg>555-013-4827</li>
        <li><svg viewBox="0 0 24 24"><path d="M2 5h20v14H2zm2 2v.5l8 5 8-5V7z"/></svg>marcustellan@veltrano.co</li>
        <li><svg viewBox="0 0 24 24"><circle cx="12" cy="12" r="10"/></svg>www.veltrano.co</li>
      </ul>
    </div>
  </section>

  <section class="card card-front">
    <div class="polar-art" role="img" aria-label="Silhouette illustration of a polar bear and two penguins under stars"></div>
    <div class="brand">
      <div class="brand-name">Veltrano.co</div>
      <div class="brand-tagline">Polar Expeditions Specialists</div>
    </div>
  </section>
</main>
</body>
</html>
```